Tall Fern Roofing Business Card

Need a business card with the logo that was designed here

Contact Information for Business Card

Name, Title, Phone, Email, Website, Company name

```html
<!DOCTYPE html>
<html lang="en">
<head>
<meta charset="utf-8">
<title>Tall Fern Roofing – Business Card</title>
<link href="https://fonts.googleapis.com/css2?family=Arimo:wght@400;700&display=swap" rel="stylesheet">
<style>
  :root {
    --stage: #2d2d2d;
    --card: #000000;
    --brand-blue: #1f78c8;
    --text-grey: #c9c9c9;
    --shadow: rgba(0, 0, 0, 0.55);
  }
  * { margin: 0; padding: 0; box-sizing: border-box; }
  html, body {
    width: 1200px;
    height: 1015px;
    overflow: hidden;
    background: var(--stage);
    font-family: "Arimo", Arial, sans-serif;
  }
  .stage {
    position: relative;
    width: 1200px;
    height: 1015px;
  }
  .card {
    position: absolute;
    left: 290px;
    width: 620px;
    height: 354px;
    background: var(--card);
    box-shadow: 0 14px 30px var(--shadow);
    overflow: hidden;
  }
  .card--front { top: 95px; }
  .card--back { top: 560px; }
  .card__stripe {
    position: absolute;
    left: 0;
    right: 0;
    bottom: 0;
    height: 12px;
    background: var(--brand-blue);
  }
  .wordmark {
    display: flex;
    align-items: center;
    gap: 12px;
    color: var(--brand-blue);
    font-weight: 700;
    letter-spacing: 1px;
    white-space: nowrap;
  }
  .wordmark__square {
    width: 18px;
    height: 18px;
    background: var(--brand-blue);
    flex: none;
  }
  .card--front .wordmark {
    position: absolute;
    left: 50%;
    top: 46%;
    transform: translate(-50%, -50%);
    font-size: 40px;
  }
  .card--front .wordmark__square { width: 26px; height: 26px; }
  .card--back .wordmark {
    position: absolute;
    right: 40px;
    top: 92px;
    font-size: 27px;
  }
  .contact {
    position: absolute;
    left: 46px;
    top: 150px;
  }
  .contact__name {
    color: var(--brand-blue);
    font-weight: 700;
    font-size: 25px;
    letter-spacing: 0.5px;
    text-transform: uppercase;
  }
  .contact__title {
    color: var(--text-grey);
    font-size: 15px;
    letter-spacing: 0.5px;
    text-transform: uppercase;
    margin-top: 4px;
  }
  .contact__rule {
    width: 130px;
    height: 1px;
    background: var(--brand-blue);
    margin: 16px 0 14px 20px;
  }
  .contact__list { list-style: none; margin-left: 20px; }
  .contact__item {
    display: flex;
    align-items: center;
    gap: 10px;
    color: var(--text-grey);
    font-size: 17px;
    line-height: 26px;
  }
  .contact__item svg { width: 16px; height: 16px; flex: none; }
</style>
</head>
<body>
<main class="stage">

  <section class="card card--front" aria-label="Card front">
    <div class="wordmark"><span class="wordmark__square"></span>Tall Fern Roofing</div>
    <div class="card__stripe"></div>
  </section>

  <section class="card card--back" aria-label="Card back">
    <div class="contact">
      <p class="contact__name">Marcus Hale</p>
      <p class="contact__title">Managing Director</p>
      <div class="contact__rule"></div>
      <ul class="contact__list">
        <li class="contact__item">
          <svg viewBox="0 0 24 24" aria-hidden="true"><path fill="#1f78c8" d="M6.6 10.8a15.1 15.1 0 0 0 6.6 6.6l2.2-2.2c.3-.3.7-.4 1-.2 1.1.4 2.3.6 3.6.6.6 0 1 .4 1 1V20c0 .6-.4 1-1 1A17 17 0 0 1 3 4c0-.6.4-1 1-1h3.5c.6 0 1 .4 1 1 0 1.3.2 2.5.6 3.6.1.3 0 .7-.2 1z"/></svg>
          044-555 019 274
        </li>
        <li class="contact__item">
          <svg viewBox="0 0 24 24" aria-hidden="true"><path fill="#1f78c8" d="M2 5h20v14H2zm2 2v.5l8 5 8-5V7l-8 5z"/></svg>
          info@tallfernroofing.com
        </li>
        <li class="contact__item">
          <svg viewBox="0 0 24 24" aria-hidden="true"><g fill="none" stroke="#1f78c8" stroke-width="2"><circle cx="12" cy="12" r="9"/><path d="M3 12h18M12 3c3 3 3 15 0 18M12 3c-3 3-3 15 0 18"/></g></svg>
          www.tallfernroofing.com
        </li>
      </ul>
    </div>
    <div class="wordmark"><span class="wordmark__square"></span>Tall Fern Roofing</div>
    <div class="card__stripe"></div>
  </section>

</main>
</body>
</html>
```